TLR PowerPoint

I am looking for a clean, corporate PowerPoint template.

I would like the following:
- title slide
- break slide
- blank slide with title (for graphs or graphics)
- an ending slide.

Target Market(s)

Business professionals, medium to large business clients.

Requirements
Must have
• Must incorporate the TLR logo in either the header or footer

```html
<!DOCTYPE html>
<html lang="en">
<head>
<meta charset="utf-8">
<title>TLR PowerPoint Template</title>
<link href="https://fonts.googleapis.com/css2?family=Noto+Serif:wght@400;700&family=Ubuntu:wght@400;500&display=swap" rel="stylesheet">
<style>
:root{
  --blue-deep:#2a56c6;
  --blue:#3f73e0;
  --blue-light:#5b8ef2;
  --blue-pale:#9dbcf8;
  --navy:#1f3f9a;
  --grey-dark:#5a5a5a;
  --grey:#7d7d7d;
  --grey-light:#b9b9b9;
  --ink:#222;
  --paper:#fff;
  --stage:#000;
  --serif:"Noto Serif",Georgia,serif;
  --sans:"Ubuntu",Arial,sans-serif;
}
*{box-sizing:border-box;margin:0;padding:0}
html,body{width:1200px;height:619px;overflow:hidden;background:var(--stage)}
.canvas{position:relative;width:1200px;height:619px}
.slide{position:absolute;width:385px;height:289px;background:var(--paper);overflow:hidden;font-family:var(--sans);color:var(--ink)}
.slide svg.bg{position:absolute;left:0;top:0}
.s-title{left:11px;top:14px}
.s-chart{left:405px;top:14px}
.s-end{left:798px;top:14px}
.s-pie{left:11px;top:318px}
.s-list{left:405px;top:318px}
.s-team{left:798px;top:318px}

.header{position:absolute;left:0;top:0;width:385px;height:32px;background:linear-gradient(90deg,var(--blue-deep),var(--blue-light));border-bottom:2px solid var(--navy)}
.header h2{font-family:var(--serif);font-weight:700;font-size:15px;color:var(--paper);position:absolute;left:10px;top:6px}
.header .mark{position:absolute;right:8px;top:5px;font-family:var(--serif);font-size:18px;color:rgba(255,255,255,.15)}

.brand{font-family:var(--serif);color:var(--navy);white-space:nowrap;letter-spacing:.3px}
.brand-lg{font-size:15px}
.brand-sm{font-size:11px}
.brand-sm.light{color:var(--paper)}

.footer-light{position:absolute;left:0;bottom:0;width:385px;height:30px;background:#f6f6f6;border-top:2px solid var(--blue)}
.footer-light .brand{position:absolute;left:6px;top:7px}
.copyright{position:absolute;font-size:6.5px;color:var(--ink)}
.footer-light .copyright{right:40px;top:12px}
.page{position:absolute;width:18px;height:18px;border-radius:50%;background:var(--blue);color:var(--paper);font-size:7px;font-weight:500;text-align:center;line-height:18px}
.footer-light .page{right:14px;top:5px}
.footer-curve{position:absolute;left:0;bottom:0;width:385px;height:28px}
.footer-curve .brand{position:absolute;left:6px;bottom:8px}
.footer-curve .copyright{right:40px;bottom:8px;color:var(--paper)}
.footer-curve .page{right:14px;bottom:3px;background:var(--paper);color:var(--blue)}

/* title slide */
.s-title h1{position:absolute;top:55px;width:100%;text-align:center;font-family:var(--serif);font-weight:700;font-size:17px;color:var(--paper)}
.s-title .sub{position:absolute;top:87px;width:100%;text-align:center;font-size:8px;line-height:14.5px;color:var(--paper)}
.s-title .brand{position:absolute;left:0;top:222px;width:100%;text-align:center}

/* chart */
.axis-label{position:absolute;font-size:6.5px;color:var(--ink)}

/* end slide */
.s-end .thanks{position:absolute;top:34px;width:100%;text-align:center;font-family:var(--serif);font-weight:700;font-size:13.5px;line-height:27px;color:var(--paper)}
.s-end .brand{position:absolute;left:0;top:142px;width:100%;text-align:center}
.s-end .person{position:absolute;top:180px;width:100%;text-align:center;font-family:var(--serif)}
.s-end .person .name{font-size:12px;font-weight:700;color:var(--blue)}
.s-end .person .role{font-size:10.5px;font-weight:700;color:var(--ink);margin-top:1px}
.contact{position:absolute;left:160px;font-size:7.5px;display:flex;align-items:center;gap:8px}
.contact .ico{width:11px;height:11px;border-radius:50%;background:var(--blue);display:block}

/* list */
.points{position:absolute;left:11px;top:57px;list-style:none;width:355px}
.points li{position:relative;padding-left:17px;font-size:7.2px;font-weight:500;line-height:12px;margin-bottom:16px}
.points li::before{content:"";position:absolute;left:0;top:1px;width:10px;height:10px;border-radius:50%;background:var(--navy)}
.points li::after{content:"";position:absolute;left:2.6px;top:4px;width:3px;height:3px;border-right:1.5px solid var(--paper);border-bottom:1.5px solid var(--paper);transform:rotate(-45deg)}

/* team */
.member{position:absolute;top:70px;width:175px;text-align:center}
.member .photo{width:74px;height:74px;border-radius:50%;margin:0 auto;border:3px solid #eef1f6}
.member .photo.a{background:radial-gradient(circle at 50% 45%,#7a7b86,#b8b8bc 70%)}
.member .photo.b{background:radial-gradient(circle at 50% 50%,#6c86b8,#e6dcc4 72%)}
.member .name{font-family:var(--serif);font-size:9.5px;color:var(--blue);margin-top:5px}
.member .role{font-size:7px;font-weight:500;margin-top:3px}
.member p{font-size:5.8px;line-height:10px;margin-top:6px;padding:0 10px}
.divider{position:absolute;left:212px;top:66px;width:1px;height:150px;background:#ccc}
</style>
</head>
<body>
<div class="canvas">

  <!-- Title slide -->
  <section class="slide s-title">
    <svg class="bg" width="385" height="289" viewBox="0 0 385 289">
      <defs>
        <linearGradient id="gTitle" x1="0" y1="0" x2="1" y2="0">
          <stop offset="0" stop-color="#2f5bcc"/><stop offset=".55" stop-color="#5b8ef2"/><stop offset="1" stop-color="#2a56c6"/>
        </linearGradient>
      </defs>
      <rect width="385" height="289" fill="url(#gTitle)"/>
      <path d="M110 180 Q260 158 385 190 L385 200 Q260 172 110 182Z" fill="#a9a9a9"/>
      <path d="M0 212 Q170 168 385 193 L385 289 L0 289Z" fill="#fff"/>
      <rect y="279" width="385" height="10" fill="#3a67d6"/>
    </svg>
    <h1>PROJECT TITLE HERE</h1>
    <div class="sub">Lorem ipsum dolor sit&nbsp; Lorem ipsum dolor sit<br>Lorem ipsum dolor sit&nbsp; Lorem ipsum dolor sit<br>Lorem ipsum dolor sit</div>
    <div class="brand brand-lg">TLR Tom Lyle Advisory</div>
  </section>

  <!-- Chart slide -->
  <section class="slide s-chart">
    <div class="header"><h2>Project Title here</h2><span class="mark">TLR</span></div>
    <span class="axis-label" style="left:26px;top:67px">Lorem ipsum text here</span>
    <span class="axis-label" style="left:26px;top:91px">Lorem ipsum text here</span>
    <span class="axis-label" style="left:26px;top:124px">Lorem ipsum text here</span>
    <span class="axis-label" style="left:26px;top:164px">Lorem ipsum text here</span>
    <span class="axis-label" style="left:26px;top:210px">Lorem ipsum text here</span>
    <svg class="bg" width="385" height="289" viewBox="0 0 385 289" role="img" aria-label="Bar chart">
      <line x1="98" y1="62" x2="98" y2="218" stroke="#333" stroke-width=".8"/>
      <line x1="98" y1="218" x2="372" y2="218" stroke="#333" stroke-width=".8"/>
      <rect x="98" y="167" width="18" height="51" fill="#3f6fd6"/>
      <rect x="120" y="127" width="21" height="91" fill="#5b8ef2"/>
      <rect x="145" y="143" width="21" height="75" fill="#5b8ef2"/>
      <rect x="170" y="173" width="21" height="45" fill="#2a56c6"/>
      <rect x="199" y="204" width="23" height="14" fill="#3f73e0"/>
      <rect x="226" y="213" width="27" height="5" fill="#7d7d7d"/>
      <rect x="256" y="76" width="22" height="142" fill="#2a56c6"/>
      <rect x="283" y="203" width="22" height="15" fill="#3f73e0"/>
      <rect x="309" y="210" width="21" height="8" fill="#3f73e0"/>
      <rect x="336" y="213" width="27" height="5" fill="#7d7d7d"/>
    </svg>
    <span class="axis-label" style="left:96px;top:225px">Lorem ipsum text here</span>
    <span class="axis-label" style="left:188px;top:225px">Lorem ipsum text here</span>
    <span class="axis-label" style="left:299px;top:225px">Lorem ipsum text here</span>
    <div class="footer-light"><span class="brand brand-sm">TLR Tom Lyle Advisory</span><span class="copyright">Copyright text here</span><span class="page">01</span></div>
  </section>

  <!-- Ending slide -->
  <section class="slide s-end">
    <svg class="bg" width="385" height="289" viewBox="0 0 385 289">
      <defs>
        <linearGradient id="gEnd" x1="0" y1="0" x2="1" y2="0">
          <stop offset="0" stop-color="#2f5bcc"/><stop offset=".55" stop-color="#5b8ef2"/><stop offset="1" stop-color="#2a56c6"/>
        </linearGradient>
      </defs>
      <rect width="385" height="289" fill="url(#gEnd)"/>
      <path d="M170 112 Q300 106 385 130 L385 138 Q300 116 170 114Z" fill="#a9a9a9"/>
      <path d="M0 143 Q190 98 385 128 L385 289 L0 289Z" fill="#fff"/>
      <rect y="279" width="385" height="10" fill="#3a67d6"/>
    </svg>
    <div class="thanks">Looking forward to hearing from you<br>and thank you for your time!</div>
    <div class="brand brand-lg">TLR Tom Lyle Advisory</div>
    <div class="person"><div class="name">Tom Lyle</div><div class="role">Co-founder</div></div>
    <div class="contact" style="top:217px"><span class="ico"></span>tomlyle@mailbox.com</div>
    <div class="contact" style="top:236px"><span class="ico"></span>tom.lyle</div>
    <div class="contact" style="top:255px"><span class="ico"></span>+00 123 456789 10</div>
  </section>

  <!-- Pie chart slide -->
  <section class="slide s-pie">
    <div class="header"><h2>Project Title here</h2><span class="mark">TLR</span></div>
    <svg class="bg" width="385" height="289" viewBox="0 0 385 289">
      <path d="M0 243 Q180 250 385 228 L385 289 L0 289Z" fill="#3a67d6"/>
      <path d="M0 243 Q180 250 385 228" fill="none" stroke="#1f3f9a" stroke-width="1"/>
    </svg>
    <svg class="bg" width="385" height="289" viewBox="0 0 385 289" role="img" aria-label="Pie chart" font-family="Ubuntu, sans-serif" font-size="6.5" font-weight="500" text-anchor="middle">
      <g stroke="#fff" stroke-width="1">
        <path d="M199 149 L199 54 A95 95 0 0 1 254.9 72.1Z" fill="#b9b9b9"/>
        <path d="M199 149 L254.9 72.1 A95 95 0 0 1 292.6 165.5Z" fill="#9dbcf8"/>
        <path d="M199 149 L292.6 165.5 A95 95 0 0 1 239.1 235.1Z" fill="#4a7ee8"/>
        <path d="M199 149 L239.1 235.1 A95 95 0 0 1 105.4 165.5Z" fill="#2f63d6"/>
        <path d="M199 149 L105.4 165.5 A95 95 0 0 1 144.5 71.2Z" fill="#5a5a5a"/>
        <path d="M199 149 L144.5 71.2 A95 95 0 0 1 199 54Z" fill="#7d7d7d"/>
      </g>
      <circle cx="199" cy="149" r="12" fill="#2a56c6" stroke="#fff" stroke-width="1.5"/>
      <text x="199" y="151.5" fill="#fff" font-family="Noto Serif, serif" font-size="7">TLR</text>
      <text x="218" y="83" fill="#222"><tspan x="218">Lorem</tspan><tspan x="218" dy="9">ipsum</tspan><tspan x="218" dy="9">dolor</tspan></text>
      <text x="181" y="83" fill="#fff"><tspan x="181">Lorem</tspan><tspan x="181" dy="9">ipsum</tspan><tspan x="181" dy="9">dolor</tspan></text>
      <text x="254" y="138" fill="#222"><tspan x="254">Lorem ipsum</tspan><tspan x="254" dy="9">dolor</tspan></text>
      <text x="245" y="192" fill="#222"><tspan x="245">Lorem ipsum</tspan><tspan x="245" dy="9">dolor</tspan></text>
      <text x="173" y="195" fill="#222"><tspan x="173">Lorem ipsum dolor</tspan><tspan x="173" dy="9">Lorem ipsum dolor</tspan></text>
      <text x="146" y="134" fill="#fff"><tspan x="146">Lorem ipsum dolor</tspan><tspan x="146" dy="9">Lorem ipsum dolor</tspan></text>
    </svg>
    <div class="footer-curve"><span class="brand brand-sm light">TLR Tom Lyle Advisory</span><span class="copyright">Copyright text here</span><span class="page">01</span></div>
  </section>

  <!-- Bullet list slide -->
  <section class="slide s-list">
    <div class="header"><h2>Project Title here</h2><span class="mark">TLR</span></div>
    <svg class="bg" width="385" height="289" viewBox="0 0 385 289">
      <path d="M0 258 Q200 262 385 236 L385 289 L0 289Z" fill="#3a67d6"/>
      <path d="M0 258 Q200 262 385 236" fill="none" stroke="#1f3f9a" stroke-width="1"/>
    </svg>
    <ul class="points">
      <li>Lorem ipsum dolor sit ipsum Lorem ipsum dolor sit ipsum Lorem ipsum dolor sit ipsum</li>
      <li>Lorem ipsum dolor sit ipsum Lorem ipsum dolor sit ipsum Lorem ipsum dolor sit ipsumLorem ipsum dolor sit ipsum Lorem ipsum dolor</li>
      <li>Lorem Lorem ipsum dolor sit ipsum Lorem ipsum dolor sit ipsum Lorem ipsum dolor sit ipsum Lorem ipsum dolor sit ipsum Lorem ipsum dolor sit ipsum Lorem ipsum dolor sit ipsumipsum dolor sit ipsum Lorem ipsum dolor sit ipsum Lorem ipsum dolor sit ipsum</li>
      <li>Lorem ipsum dolor sit ipsum Lorem ipsum dolor sit ipsum Lorem ipsum dolor sit ipsumLorem ipsum dolor sit ipsum Lorem ipsum dolor</li>
    </ul>
    <div class="footer-curve"><span class="brand brand-sm light">TLR Tom Lyle Advisory</span><span class="copyright">Copyright text here</span><span class="page">01</span></div>
  </section>

  <!-- Team slide -->
  <section class="slide s-team">
    <div class="header"><h2>Project Title here</h2><span class="mark">TLR</span></div>
    <div class="member" style="left:5px">
      <div class="photo a" role="img" aria-label="Portrait photo of first co-founder"></div>
      <div class="name">Lorem ipsum</div>
      <div class="role">Co-Founder</div>
      <p>Lorem ipsum dolor sit ipsum Lorem ipsum dolor sit ipsumLorem ipsum dolor sit ipsum Lorem ipsum dolor sit ipsumLorem ipsum dolor sit ipsum Lorem ipsum dolor sit ipsumLorem ipsum dolor sit ipsum</p>
    </div>
    <div class="divider"></div>
    <div class="member" style="left:220px">
      <div class="photo b" role="img" aria-label="Portrait photo of second co-founder"></div>
      <div class="name">Lorem ipsum dolor</div>
      <div class="role">Co-Founder</div>
      <p>Lorem ipsum dolor sit ipsum Lorem ipsum dolor sit ipsumLorem ipsum dolor sit ipsum Lorem ipsum dolor sit ipsumLorem ipsum dolor sit ipsum Lorem ipsum dolor sit ipsumLorem ipsum dolor sit ipsum</p>
    </div>
    <div class="footer-light"><span class="brand brand-sm">TLR Tom Lyle Advisory</span><span class="copyright">Copyright text here</span><span class="page">01</span></div>
  </section>

</div>
</body>
</html>
```